Brivolt Technologies business card design

We need a business card designed with our new logo. it would be great if the card could communicate it is a technology based company.

Target Market(s)

system integrators

Industry/Entity Type

technology, IOT

Contact Information for Business Card

Name, designation, Address, telephone number, email address

Requirements
Must have
• logo and company name
Nice to have
• something to do with technology

```html
<!DOCTYPE html>
<html lang="en">
<head>
<meta charset="UTF-8">
<title>Brivolt Technologies Business Card</title>
<link href="https://fonts.googleapis.com/css2?family=Open+Sans:wght@400;600;700&display=swap" rel="stylesheet">
<style>
  :root {
    --stage: #3b3b3b;
    --card: #1b1b1b;
    --card-deep: #141414;
    --accent: #f7941d;
    --ink: #e9e9e9;
    --pattern-light: #2a2a2a;
    --pattern-dark: #0d0d0d;
  }
  * { margin: 0; padding: 0; box-sizing: border-box; }
  html, body {
    width: 1200px; height: 801px; overflow: hidden;
    background: var(--stage);
    font-family: "Open Sans", Arial, sans-serif;
  }
  .stage {
    width: 1200px; height: 801px;
    display: flex; align-items: center; justify-content: center; gap: 40px;
  }
  .card {
    position: relative;
    width: 540px; height: 309px;
    background: var(--card);
    border-bottom: 3px solid var(--accent);
    border-left: 2px solid var(--accent);
    box-shadow: 0 18px 40px rgba(0,0,0,0.45);
    overflow: hidden;
  }
  /* Front */
  .brand {
    position: absolute; left: 44px; top: 92px;
    display: flex; align-items: center; gap: 12px;
  }
  .brand-mark { width: 26px; height: 26px; background: var(--accent); }
  .brand-name {
    color: var(--ink); font-weight: 700; font-size: 25px;
    letter-spacing: 1px; text-transform: uppercase; line-height: 1.1;
  }
  .person {
    position: absolute; right: 40px; top: 40px; text-align: right;
  }
  .person-name {
    color: var(--accent); font-weight: 700; font-size: 19px;
    text-transform: uppercase; letter-spacing: 0.3px;
  }
  .person-role { color: var(--ink); font-size: 13px; margin-top: 1px; }
  .person-rule {
    width: 230px; height: 1px; background: var(--accent);
    margin: 8px 0 10px auto;
  }
  .address { color: var(--ink); font-size: 13px; line-height: 1.5; }
  .contact {
    position: absolute; left: 40px; bottom: 26px; width: 300px;
  }
  .contact-rule { height: 1px; background: var(--accent); margin-bottom: 12px; }
  .contact-list { list-style: none; }
  .contact-list li {
    display: flex; align-items: center; gap: 9px;
    color: var(--ink); font-size: 13px; line-height: 1.6;
  }
  .contact-list svg { width: 11px; height: 11px; fill: var(--accent); flex: none; }
  /* Back */
  .card-back { background: var(--card-deep); }
  .back-pattern {
    position: absolute; inset: 0;
    background: linear-gradient(135deg, var(--pattern-dark) 0%, var(--card-deep) 45%, var(--pattern-light) 100%);
  }
  .back-brand {
    position: absolute; right: 48px; top: 50%; transform: translateY(-50%);
    display: flex; align-items: center; gap: 10px;
  }
  .back-brand .brand-name { font-size: 20px; }
  .back-brand .brand-mark { width: 20px; height: 20px; }
</style>
</head>
<body>
<main class="stage">
  <section class="card card-front" aria-label="Business card front">
    <div class="brand">
      <span class="brand-mark"></span>
      <span class="brand-name">Brivolt<br>Technologies</span>
    </div>
    <div class="person">
      <p class="person-name">Daniel Morrow</p>
      <p class="person-role">President</p>
      <div class="person-rule"></div>
      <p class="address">1180 Harbor Crest Drive<br>Seaview CA 92601</p>
    </div>
    <div class="contact">
      <div class="contact-rule"></div>
      <ul class="contact-list">
        <li><svg viewBox="0 0 12 12"><path d="M2.5 1l2 2.2-1 1.2c.7 1.5 1.9 2.7 3.4 3.4l1.2-1 2.2 2-1 1.7C5 10.3 1.7 7 .8 2z"/></svg>949-555-0172</li>
        <li><svg viewBox="0 0 12 12"><path d="M0 2h12v8H0z M0 2l6 4 6-4" /></svg>info@brivolttechnologies.com</li>
        <li><svg viewBox="0 0 12 12"><circle cx="6" cy="6" r="6"/></svg>www.brivolttechnologies.com</li>
      </ul>
    </div>
  </section>
  <section class="card card-back" aria-label="Business card back">
    <div class="back-pattern" role="img" aria-label="Repeating tonal pattern of the brand mark in glossy black"></div>
    <div class="back-brand">
      <span class="brand-mark"></span>
      <span class="brand-name">Brivolt</span>
    </div>
  </section>
</main>
</body>
</html>
```